Local Roofing Company Billboard Design

We need a billboard design for an 8' x 32' billboard. This billboard would need to be easily readable and stand out well.
I have uploaded a design that we like - simple, readable, and gets the point across. We do NOT want the $1000 off offer included.
We are looking for a black background with white copy so it will stand out. We want the following on the billboard:
Brindlewick Roofing logo
brindlewick-roofing.example (optional)
555.214.7730 (mandatory)
Photo is optional, depends on how it all lays out
Production file must comply with layout requirements (uploaded).
Target Market(s)
Homeowners
Font styles to use
Other font styles liked:
- match font from logo
Colors
Designer to choose colors to be used in the design.
Requirements
Must have
- Black background, white copy, logo must be large and legible. Colors used must match our logo colors.

```html
<!DOCTYPE html>
<html lang="en">
<head>
<meta charset="utf-8">
<title>Brindlewick Roofing Billboard</title>
<link rel="stylesheet" href="https://fonts.googleapis.com/css2?family=Arvo:wght@700&family=Oswald:wght@600&family=Montserrat:wght@500&display=swap">
<style>
  :root {
    --brand-orange: #e55a1f;
    --brand-black: #000000;
    --paper: #ffffff;
    --photo-light: #f4f1ee;
    --photo-mid: #b9b2aa;
    --photo-roof: #3f4347;
    --photo-accent: #d9782f;
  }
  html, body {
    margin: 0;
    padding: 0;
    width: 1200px;
    height: 1051px;
    overflow: hidden;
    background: var(--paper);
  }
  .stage {
    position: relative;
    width: 1200px;
    height: 1051px;
  }
  .billboard {
    position: absolute;
    left: 60px;
    top: 390px;
    width: 1080px;
    height: 270px;
    filter: drop-shadow(0 14px 22px rgba(0,0,0,0.22));
  }
  .brand-name {
    font-family: "Arvo", serif;
    font-weight: 700;
    font-size: 96px;
    fill: var(--paper);
  }
  .phone-number {
    font-family: "Oswald", sans-serif;
    font-weight: 600;
    font-size: 132px;
    fill: var(--brand-black);
  }
  .web-address {
    font-family: "Montserrat", sans-serif;
    font-weight: 500;
    font-size: 36px;
    fill: var(--paper);
  }
</style>
</head>
<body>
<main class="stage">
  <svg class="billboard" viewBox="0 0 1764 441" xmlns="http://www.w3.org/2000/svg">
    <defs>
      <linearGradient id="photoTone" x1="0" y1="0" x2="0" y2="1">
        <stop offset="0" stop-color="var(--photo-light)"/>
        <stop offset="0.55" stop-color="var(--photo-mid)"/>
        <stop offset="0.8" stop-color="var(--photo-roof)"/>
        <stop offset="1" stop-color="var(--photo-roof)"/>
      </linearGradient>
      <linearGradient id="photoWarm" x1="0" y1="0" x2="1" y2="0">
        <stop offset="0" stop-color="var(--photo-accent)" stop-opacity="0.55"/>
        <stop offset="0.35" stop-color="var(--photo-accent)" stop-opacity="0"/>
      </linearGradient>
    </defs>

    <rect class="board-base" width="1764" height="441" fill="var(--paper)"/>

    <g class="roofer-photo" role="img" aria-label="Photo of a roofer in an orange safety jacket nailing asphalt shingles with a nail gun">
      <polygon points="0,0 980,0 740,320 0,320" fill="url(#photoTone)"/>
      <polygon points="0,0 980,0 740,320 0,320" fill="url(#photoWarm)"/>
    </g>

    <polygon class="web-band" points="0,320 740,320 650,441 0,441" fill="var(--brand-orange)"/>

    <polygon class="phone-band" points="998,0 1764,0 1764,441 668,441" fill="var(--brand-orange)"/>
    <polygon class="brand-panel" points="1016,0 1764,0 1764,253 827,253" fill="var(--brand-black)"/>

    <g class="brand-name" text-anchor="middle">
      <text x="1395" y="112" textLength="690" lengthAdjust="spacingAndGlyphs">Brindlewick</text>
      <text x="1395" y="222">Roofing</text>
    </g>

    <g class="phone-icon" fill="var(--brand-black)">
      <path d="M822,318 c10,-8 18,-6 24,4 l10,18 c4,8 2,14 -6,18 l-8,4 c4,14 14,26 28,32 l5,-8 c5,-7 11,-8 18,-4 l17,10 c9,6 10,14 2,22 c-12,12 -30,14 -48,4 c-26,-14 -46,-40 -52,-66 c-3,-14 0,-26 10,-34 z"/>
      <path d="M862,322 a22,22 0 0 1 22,22" fill="none" stroke="var(--brand-black)" stroke-width="6" stroke-linecap="round"/>
      <path d="M864,304 a40,40 0 0 1 40,40" fill="none" stroke="var(--brand-black)" stroke-width="6" stroke-linecap="round"/>
    </g>
    <text class="phone-number" x="918" y="402" textLength="782" lengthAdjust="spacingAndGlyphs">555-214-7730</text>

    <g class="web-icon" fill="none" stroke="var(--paper)">
      <rect x="48" y="356" width="42" height="30" rx="3" stroke-width="6"/>
      <rect x="40" y="391" width="58" height="6" rx="2" fill="var(--paper)" stroke="none"/>
    </g>
    <text class="web-address" x="116" y="393" textLength="520" lengthAdjust="spacingAndGlyphs">brindlewick-roofing.example</text>
  </svg>
</main>
</body>
</html>
```